Maple Roster Business Card for recruitment company

We are looking for a Business Card Design that incorporates our personal details and our busines name and logo. We are a specialized search consultancy that recruit Property and Construction professionals.
We would like a business card that stands out and is appealing to the Construction and Property industry as well.

Target Market(s)

people in the construction and property industry

Contact Information for Business Card

Business Name and logo

Font styles to use
Serif

Colors
0094D4
00A9DD
6FCCEA
C7EBF8
E9F6FB

Requirements
Must have
• Business name and logo as well as contact details
Should not have
• No photos of us please

```html
<!DOCTYPE html>
<html lang="en">
<head>
<meta charset="utf-8">
<title>Maple Roster — Business Card</title>
<link href="https://fonts.googleapis.com/css2?family=Libre+Baskerville:wght@400;700&display=swap" rel="stylesheet">
<style>
  :root {
    --bg: #e4e4e4;
    --card: #f7f7f7;
    --blue: #1e96d6;
    --icon-blue: #12a6e0;
    --charcoal: #3a3a3a;
    --ink: #2b2b2b;
    --logo-ink: #1f3b4d;
  }
  html, body {
    margin: 0;
    width: 1200px;
    height: 899px;
    overflow: hidden;
    background: var(--bg);
  }
  .card {
    position: absolute;
    left: 150px;
    top: 192px;
    width: 900px;
    height: 514px;
    background: var(--card);
    box-shadow: 0 18px 40px rgba(0,0,0,0.18);
    font-family: "Libre Baskerville", Georgia, serif;
    color: var(--ink);
    overflow: hidden;
  }
  .accent-strip {
    position: absolute;
    left: 0;
    top: 34px;
    width: 24px;
    height: 96px;
    background: var(--blue);
  }
  .brand-name {
    position: absolute;
    left: 110px;
    top: 62px;
    margin: 0;
    font-size: 40px;
    font-weight: 400;
    letter-spacing: 3px;
    text-transform: uppercase;
    color: var(--logo-ink);
  }
  .holder {
    position: absolute;
    right: 34px;
    top: 150px;
    text-align: right;
  }
  .holder-name {
    margin: 0;
    font-size: 27px;
    letter-spacing: 1px;
    text-transform: uppercase;
  }
  .holder-role {
    margin: 4px 0 0;
    font-size: 20px;
    display: inline-block;
    position: relative;
    padding-bottom: 8px;
  }
  .holder-role::after {
    content: "";
    position: absolute;
    right: 0;
    bottom: 0;
    width: 96px;
    height: 2px;
    background: var(--blue);
  }
  .contacts {
    position: absolute;
    right: 34px;
    top: 262px;
    margin: 0;
    padding: 0;
    list-style: none;
    font-size: 17px;
    line-height: 1.3;
  }
  .contact {
    display: flex;
    justify-content: flex-end;
    align-items: center;
    gap: 18px;
    margin-bottom: 10px;
    text-align: right;
  }
  .contact.address { margin-bottom: 16px; }
  .icon {
    width: 28px;
    height: 28px;
    flex: none;
  }
  .bottom-bands {
    position: absolute;
    left: 0;
    bottom: 0;
    width: 900px;
    height: 44px;
  }
</style>
</head>
<body>
  <div class="card">
    <div class="accent-strip"></div>
    <h1 class="brand-name">Maple Roster</h1>

    <div class="holder">
      <p class="holder-name">Daniel R. Whitcombe</p>
      <p class="holder-role">Managing Director</p>
    </div>

    <ul class="contacts">
      <li class="contact address">
        <span>2714 Harbor Crest Avenue<br>Portland, OR 97205</span>
        <svg class="icon" viewBox="0 0 28 28" aria-hidden="true">
          <rect width="28" height="28" rx="5" fill="var(--charcoal)"/>
          <path d="M14 6a6 6 0 0 0-6 6c0 4.5 6 10 6 10s6-5.5 6-10a6 6 0 0 0-6-6z" fill="#fff"/>
          <circle cx="14" cy="12" r="2.4" fill="var(--charcoal)"/>
        </svg>
      </li>
      <li class="contact">
        <span>+00 321 654 87</span>
        <svg class="icon" viewBox="0 0 28 28" aria-hidden="true">
          <rect width="28" height="28" rx="5" fill="var(--icon-blue)"/>
          <path d="M9 7l3 0 1.5 4-2 1.5c1 2 2.5 3.5 4.5 4.5l1.5-2 4 1.5v3c0 1-1 2-2 2C12 21.5 6.5 16 6.5 9c0-1 1-2 2.5-2z" fill="#fff"/>
        </svg>
      </li>
      <li class="contact">
        <span>hello@mapleroster.com</span>
        <svg class="icon" viewBox="0 0 28 28" aria-hidden="true">
          <rect width="28" height="28" rx="5" fill="var(--icon-blue)"/>
          <rect x="6" y="8.5" width="16" height="11" fill="none" stroke="#fff" stroke-width="1.8"/>
          <path d="M6 8.5l8 6.5 8-6.5" fill="none" stroke="#fff" stroke-width="1.8"/>
        </svg>
      </li>
      <li class="contact">
        <span>www.mapleroster.com</span>
        <svg class="icon" viewBox="0 0 28 28" aria-hidden="true">
          <rect width="28" height="28" rx="5" fill="var(--icon-blue)"/>
          <path d="M10 7l0 14 3.5-3.5 2.5 5 2.2-1-2.5-5h5z" fill="#fff"/>
        </svg>
      </li>
    </ul>

    <svg class="bottom-bands" viewBox="0 0 900 44" preserveAspectRatio="none" aria-hidden="true">
      <polygon points="0,0 470,0 440,44 0,44" fill="var(--charcoal)"/>
      <polygon points="490,0 900,0 900,44 460,44" fill="var(--blue)"/>
    </svg>
  </div>
</body>
</html>
```